Business Cards for a law firm

Business cards for our law firm. Use our silhoette logo and OAK PARTNERS - check our website (www.oakpartners.example)

Contact Information for Business Card

our silhouette logo, OAK PARTNERS, 800-555-0147, Dorian Pemberton, dorian@oakpartners.example

Requirements
Must have
• our silhouette logo, OAK PARTNERS, 800-555-0147, Dorian Pemberton, dorian@oakpartners.example

```html
<!DOCTYPE html>
<html lang="en">
<head>
<meta charset="utf-8">
<title>Oak Partners — Business Card</title>
<link href="https://fonts.googleapis.com/css2?family=Montserrat:wght@400;500;600;700&display=swap" rel="stylesheet">
<style>
  :root {
    --navy: #1f2f6b;
    --navy-deep: #182557;
    --navy-emboss: #2a3b7c;
    --paper: #ffffff;
    --paper-shade: #ececee;
    --ink: #1c2340;
    --backdrop: #e4e5e8;
  }
  html, body {
    margin: 0;
    width: 1200px;
    height: 900px;
    overflow: hidden;
    background: var(--backdrop);
    font-family: "Montserrat", sans-serif;
  }
  .sheet {
    width: 1200px;
    height: 900px;
    display: flex;
    flex-direction: column;
    align-items: center;
    justify-content: center;
    gap: 40px;
  }
  .card {
    position: relative;
    width: 700px;
    height: 400px;
    border-radius: 26px;
    overflow: hidden;
    box-shadow: 0 10px 28px rgba(20, 25, 50, 0.25);
  }
  .card--front {
    background: linear-gradient(180deg, var(--paper) 0%, var(--paper-shade) 100%);
  }
  .card--back {
    background: var(--navy);
  }

  /* Front */
  .firm-name {
    position: absolute;
    left: 56px;
    top: 60px;
    margin: 0;
    font-weight: 700;
    font-size: 33px;
    letter-spacing: 2.5px;
    white-space: nowrap;
    color: var(--navy);
  }
  .edge-tab {
    position: absolute;
    left: 0;
    top: 160px;
    width: 20px;
    height: 38px;
    background: var(--navy);
    border-radius: 0 5px 5px 0;
  }
  .person {
    position: absolute;
    left: 68px;
    top: 150px;
  }
  .person__name {
    margin: 0;
    font-weight: 700;
    font-size: 24px;
    letter-spacing: 1.5px;
    white-space: nowrap;
    color: var(--navy);
  }
  .person__role {
    margin: 2px 0 0;
    font-size: 14px;
    letter-spacing: 1px;
    color: var(--ink);
  }
  .address {
    position: absolute;
    left: 68px;
    top: 228px;
    margin: 0;
    font-style: normal;
    font-size: 15px;
    line-height: 1.3;
    letter-spacing: 0.6px;
    color: var(--ink);
  }
  .contact-list {
    position: absolute;
    left: 68px;
    top: 290px;
    margin: 0;
    padding: 0;
    list-style: none;
    font-size: 15px;
    letter-spacing: 0.6px;
    color: var(--ink);
  }
  .contact-list li {
    display: flex;
    align-items: center;
    gap: 12px;
    height: 26px;
    white-space: nowrap;
  }
  .contact-list svg {
    width: 15px;
    height: 15px;
    fill: var(--navy);
  }
  .logo-area--front {
    position: absolute;
    right: 44px;
    top: 46px;
    width: 210px;
    height: 310px;
    border-radius: 8px;
    background: linear-gradient(180deg, #2a3b7e 0%, var(--navy) 100%);
  }

  /* Back */
  .logo-area--back {
    position: absolute;
    left: 60px;
    top: 110px;
    width: 290px;
    height: 260px;
    border-radius: 8px;
    background: linear-gradient(180deg, var(--navy-emboss) 0%, var(--navy-deep) 100%);
  }
  .back-name {
    position: absolute;
    right: 56px;
    top: 60px;
    margin: 0;
    font-weight: 600;
    font-size: 36px;
    letter-spacing: 3px;
    white-space: nowrap;
    color: var(--navy-emboss);
  }
</style>
</head>
<body>
<main class="sheet">

  <section class="card card--front" aria-label="Business card front">
    <h1 class="firm-name">OAK PARTNERS</h1>
    <span class="edge-tab"></span>
    <div class="person">
      <p class="person__name">DORIAN PEMBERTON</p>
      <p class="person__role">OWNER</p>
    </div>
    <address class="address">1420 Harbor View Ave #310,<br>Lakemont, CA 90000</address>
    <ul class="contact-list">
      <li>
        <svg viewBox="0 0 16 16" aria-hidden="true"><path d="M3.5 1.5l2.4 2.6-1.3 1.7c.8 1.9 2.3 3.4 4.3 4.4l1.7-1.3 2.6 2.4-1.5 2.2C6.8 13.2 2.8 9.2 1.3 3l2.2-1.5z"/></svg>
        800-555-0147
      </li>
      <li>
        <svg viewBox="0 0 16 16" aria-hidden="true"><path d="M1 3h14v10H1V3zm1.6 1.5L8 8.6l5.4-4.1H2.6zM2.5 5.8v5.7h11V5.8L8 10 2.5 5.8z"/></svg>
        dorian@oakpartners.example
      </li>
      <li>
        <svg viewBox="0 0 16 16" aria-hidden="true"><circle cx="8" cy="8" r="7"/><path d="M4 5c1.5.4 2.4 1.4 2 3-.3 1.3 1 2 1 3.5M10 2.5c-.3 1.5.6 2.4 2 2.6M11.5 9c-.8.6-1 1.6-.6 2.6" stroke="#fff" stroke-width="1" fill="none"/></svg>
        www.oakpartners.example
      </li>
    </ul>
    <div class="logo-area--front" role="img" aria-label="Firm silhouette logo of two standing figures"></div>
  </section>

  <section class="card card--back" aria-label="Business card back">
    <div class="logo-area--back" role="img" aria-label="Embossed firm silhouette logo of two standing figures"></div>
    <p class="back-name">OAK PARTNERS</p>
  </section>

</main>
</body>
</html>
```